Road Construction Company needs business cards

We would like a new business card designed for our business.

We're a road construction company based in Qld, Australia.

Can the business card please have the following information on it.

Name: Warren Halbeck
Position: General Manager
Phone: 0472 915 348
Email: Warren.halbeck@tovrin.com.au
Address: 87 Marrow Ave, Pendlebay, QLD, 4023
Website: www.tovrin.com.au

Visually we'd like the card to be professional and simple.

Attached is our logo.

Our website is www.tovrin.com.au

Target Market(s)

Men aged 25-60

Contact Information for Business Card

As listed in project description

Font styles to use
Serif

Requirements
Must have
• Large logo on back of card

```html
<!DOCTYPE html>
<html lang="en">
<head>
<meta charset="utf-8">
<title>Tovrin Business Card</title>
<link rel="stylesheet" href="https://fonts.googleapis.com/css2?family=Poppins:wght@300;400;600;800&display=swap">
<style>
  :root {
    --bg: #2a2a2b;
    --brand-blue: #1356b8;
    --brand-blue-deep: #0d4ca6;
    --accent-blue: #3aa3dc;
    --paper: #fbfbfb;
    --ink-light: #ffffff;
  }
  * { margin: 0; padding: 0; box-sizing: border-box; }
  html, body {
    width: 1200px; height: 904px; overflow: hidden;
    background: var(--bg);
    font-family: "Poppins", sans-serif;
  }
  .stage {
    position: relative; width: 1200px; height: 904px;
    display: flex; flex-direction: column; align-items: center; justify-content: center; gap: 56px;
  }
  .card {
    position: relative; width: 560px; height: 320px; overflow: hidden;
    box-shadow: 0 10px 28px rgba(0,0,0,.45);
  }
  .card-front { background: var(--paper); }
  .card-front .shapes { position: absolute; inset: 0; }
  .contact-block {
    position: absolute; left: 44px; top: 74px; color: var(--ink-light);
  }
  .person-name { font-size: 22px; font-weight: 600; line-height: 1.1; }
  .person-role { font-size: 14px; font-weight: 300; color: var(--accent-blue); margin-top: 2px; }
  .rule { width: 22px; height: 2px; background: var(--accent-blue); margin: 12px 0 12px; }
  .address { font-size: 11.5px; font-weight: 400; line-height: 1.45; margin-bottom: 6px; }
  .contact-list { list-style: none; font-size: 11.5px; line-height: 1.55; }
  .contact-list li { display: flex; align-items: center; gap: 8px; }
  .contact-list svg { width: 10px; height: 10px; flex: none; }
  .front-wordmark {
    position: absolute; left: 342px; top: 128px;
    font-size: 40px; font-weight: 800; letter-spacing: 1px; color: var(--brand-blue);
  }
  .card-back {
    background: linear-gradient(160deg, var(--brand-blue) 0%, var(--brand-blue-deep) 100%);
    display: flex; align-items: center; justify-content: center;
  }
  .back-wordmark {
    font-size: 68px; font-weight: 800; letter-spacing: 2px; color: var(--ink-light);
  }
</style>
</head>
<body>
<main class="stage">
  <section class="card card-front" aria-label="Business card front">
    <svg class="shapes" viewBox="0 0 560 320" width="560" height="320" aria-hidden="true">
      <polygon points="0,0 200,0 368,320 0,320" fill="var(--brand-blue)"/>
      <polygon points="200,0 224,0 374,320 368,320" fill="var(--accent-blue)"/>
    </svg>
    <div class="contact-block">
      <h1 class="person-name">Warren Halbeck</h1>
      <p class="person-role">General Manager</p>
      <div class="rule"></div>
      <p class="address">87 Marrow Ave,<br>Pendlebay, QLD, 4023</p>
      <ul class="contact-list">
        <li>
          <svg viewBox="0 0 10 10"><path d="M2 1 L4 3 L3 4 Q4.5 6 6 7 L7 6 L9 8 L8 9 Q4 9 1 5 Q1 2 2 1Z" fill="var(--accent-blue)"/></svg>
          0472 915 348
        </li>
        <li>
          <svg viewBox="0 0 10 10"><rect x="0.5" y="2" width="9" height="6.5" fill="var(--accent-blue)"/><path d="M0.5 2 L5 5.5 L9.5 2" stroke="var(--brand-blue)" stroke-width="0.9" fill="none"/></svg>
          Warren.halbeck@tovrin.com.au
        </li>
        <li>
          <svg viewBox="0 0 10 10"><circle cx="5" cy="5" r="4.2" fill="none" stroke="var(--accent-blue)" stroke-width="1"/><ellipse cx="5" cy="5" rx="1.8" ry="4.2" fill="none" stroke="var(--accent-blue)" stroke-width="0.8"/><line x1="0.8" y1="5" x2="9.2" y2="5" stroke="var(--accent-blue)" stroke-width="0.8"/></svg>
          www.tovrin.com.au
        </li>
      </ul>
    </div>
    <div class="front-wordmark">TOVRIN</div>
  </section>

  <section class="card card-back" aria-label="Business card back">
    <div class="back-wordmark">TOVRIN</div>
  </section>
</main>
</body>
</html>
```